Stationery Design + Business Cards

Stationary (letterhead as A4 210x297mm and Letter 8.5"x11", preferably both master page + 2nd pages)

Also need business cards, standard size 50x88mm, can be vertical or horizontal.

You can use a front/back design for the business cards, or front only.

Looking at the uploaded file (devank, you already have that), I want it to use the first logo on the list (4 colors).

Alternative, try the grayscale version (second file).

I need the following information on the business card (in no particular order, let me know what you come up with): 

Firstname Lastlame 
Title 

Mobile +1 555-204-7391 

VelaMorn, Inc. 
24851 Birchwood Ridge Passage 
Carmel, IN 46099 
Tel. +1 555-368-4172 
Fax +1 555-619-0834 

Web: www.velamorn.example 
Twitter: twitter/VelaMorn or @VelaMorn 
Facebook: facebook.com/VelaMorn 

For letterhead, just the company name, address + phone number & fax number 

If you think the phone/fax or something else should not be on the business cards, or something could be missing, let me know.

```html
<!DOCTYPE html>
<html lang="en">
<head>
<meta charset="utf-8">
<title>VelaMorn Letterhead 210x297mm</title>
<link rel="stylesheet" href="https://fonts.googleapis.com/css2?family=Open+Sans:wght@400;700&display=swap">
<style>
  :root {
    --stage: #000000;
    --paper: #ffffff;
    --tint: #edeeee;
    --brand-blue: #1a4fa3;
    --band-blue: #0f4ea3;
    --rule-grey: #cfd0d0;
    --label: #ffffff;
    --footer-text: #ffffff;
  }
  * { box-sizing: border-box; margin: 0; padding: 0; }
  html, body {
    width: 900px;
    height: 1200px;
    overflow: hidden;
    background: var(--stage);
    font-family: "Open Sans", Arial, sans-serif;
  }
  .canvas {
    position: relative;
    width: 900px;
    height: 1200px;
    background: var(--stage);
  }
  .sheet-label {
    position: absolute;
    top: 36px;
    left: 0;
    width: 900px;
    text-align: center;
    color: var(--label);
    font-weight: 700;
    font-size: 17px;
    letter-spacing: 0.2px;
  }
  .letterhead {
    position: absolute;
    left: 50px;
    top: 68px;
    width: 775px;
    height: 1097px;
    background: var(--paper);
    overflow: hidden;
  }
  .corner-decoration {
    position: absolute;
    left: 0;
    top: 0;
    width: 470px;
    height: 460px;
  }
  .brand-name {
    position: absolute;
    right: 42px;
    top: 74px;
    display: flex;
    align-items: center;
    gap: 12px;
    color: var(--brand-blue);
    font-weight: 400;
    font-size: 43px;
    line-height: 1;
    letter-spacing: -0.5px;
  }
  .brand-dot {
    width: 16px;
    height: 16px;
    border-radius: 50%;
    background: var(--brand-blue);
  }
  .footer-rule {
    position: absolute;
    left: 0;
    top: 1057px;
    width: 100%;
    height: 4px;
    background: var(--rule-grey);
  }
  .footer-band {
    position: absolute;
    left: 0;
    top: 1065px;
    width: 100%;
    height: 32px;
    background: var(--band-blue);
    display: flex;
    align-items: center;
    justify-content: center;
    color: var(--footer-text);
    font-weight: 700;
    font-size: 10.5px;
  }
</style>
</head>
<body>
  <div class="canvas">
    <p class="sheet-label">Letter Head 210x297mm</p>

    <div class="letterhead">
      <svg class="corner-decoration" viewBox="0 0 470 460" role="img" aria-label="Faint light grey brand decoration in the top-left corner">
        <defs>
          <radialGradient id="corner-tint" cx="0.35" cy="0.3" r="0.7">
            <stop offset="0" stop-color="#edeeee" stop-opacity="1"/>
            <stop offset="1" stop-color="#edeeee" stop-opacity="0"/>
          </radialGradient>
        </defs>
        <rect width="470" height="460" fill="url(#corner-tint)"/>
      </svg>

      <div class="brand-name">
        <span class="brand-dot"></span>
        <span>VelaMorn</span>
      </div>

      <div class="footer-rule"></div>
      <div class="footer-band">
        VelaMorn, Inc., 24851 Birchwood Ridge Passage, Carmel, IN 46099, Tel. +1 555-368-4172, Fax +1 555-619-0834
      </div>
    </div>
  </div>
</body>
</html>
```